Thornbury Building Company - Card Design

I am looking to use the logo designs that you already did for me to develop a business card. I would like the card to have a black background and be double sided. I want white and green logo and text. I have attached an inspiration photo of a look that I like. I would like to use the Vertical Logo attached to take up the full front side of the card. On the back where I have my name and information, I would like to have the horizontal logo or maybe even just the image of the 'A' and trees without the text. I am open, but I am looking for something clean and simple and I want the green to really pop! Additional files can be found under Design #: 58302946

Target Market(s)

Homeowners

Industry/Entity Type

Construction

Contact Information for Business Card

Name: Marcus Thornbury, Title: Project Manager, Phone: 555.274.8136, Email: thornburybuildingcompany@mailvesta.com, address: 487 Larkspur Ln, Cedar Hollow, OR 95033, Lic# 2468317

Colors
00AB8E
00BBA5
67D7C9
C6EFE9
E9F9F6

Requirements
Nice to have
• I would like to see the logos that I have already got from ArtLoomHub, though I am open to new ones

```html
<!DOCTYPE html>
<html lang="en">
<head>
<meta charset="utf-8">
<title>Thornbury Building Company – Business Card</title>
<link href="https://fonts.googleapis.com/css2?family=Lato:wght@400;700;900&display=swap" rel="stylesheet">
<style>
  :root {
    --page: #e9e6e2;
    --card: #222121;
    --green: #6cb945;
    --white: #ffffff;
    --muted: #e8e8e8;
  }
  * { margin: 0; padding: 0; box-sizing: border-box; }
  html, body { width: 1200px; height: 977px; overflow: hidden; }
  body {
    background: var(--page);
    font-family: "Lato", sans-serif;
    position: relative;
  }
  .card {
    position: absolute;
    left: 220px;
    width: 760px;
    height: 434px;
    background: var(--card);
    border-radius: 26px;
    box-shadow: 0 10px 24px rgba(0,0,0,0.18);
    overflow: hidden;
  }
  .card--front { top: 36px; }
  .card--back { top: 507px; }

  /* Front */
  .front-mark {
    position: absolute;
    inset: 0;
    display: flex;
    align-items: center;
    justify-content: center;
    gap: 18px;
  }
  .front-mark__square {
    width: 30px; height: 30px;
    background: var(--green);
  }
  .front-mark__name {
    font-weight: 900;
    font-size: 44px;
    letter-spacing: 1px;
    color: var(--white);
    text-transform: uppercase;
    line-height: 1.1;
    text-align: left;
  }

  /* Back */
  .back-mark {
    position: absolute;
    right: 56px;
    top: 60px;
    display: flex;
    align-items: center;
    gap: 12px;
  }
  .back-mark__square { width: 20px; height: 20px; background: var(--green); }
  .back-mark__name {
    font-weight: 900;
    font-size: 22px;
    line-height: 1.15;
    color: var(--white);
    text-transform: uppercase;
    text-align: left;
  }
  .identity {
    position: absolute;
    left: 52px;
    top: 232px;
  }
  .identity__name {
    font-weight: 900;
    font-size: 34px;
    line-height: 1.1;
    color: var(--green);
    text-transform: uppercase;
    letter-spacing: -0.5px;
  }
  .identity__title {
    font-size: 20px;
    color: var(--muted);
    margin-top: 4px;
  }
  .divider {
    position: absolute;
    left: 58px;
    right: 56px;
    top: 318px;
    height: 2px;
    background: var(--green);
  }
  .address {
    position: absolute;
    right: 56px;
    top: 336px;
    text-align: right;
    font-style: normal;
    font-size: 17px;
    line-height: 1.45;
    color: var(--muted);
  }
  .contact {
    position: absolute;
    left: 56px;
    top: 334px;
    list-style: none;
  }
  .contact__item {
    display: flex;
    align-items: center;
    gap: 10px;
    font-size: 18px;
    line-height: 1.45;
    color: var(--muted);
  }
  .contact__icon { width: 14px; height: 14px; flex: none; }
</style>
</head>
<body>

<section class="card card--front" aria-label="Card front">
  <div class="front-mark">
    <div class="front-mark__square"></div>
    <div class="front-mark__name">Thornbury<br>Building Company</div>
  </div>
</section>

<section class="card card--back" aria-label="Card back">
  <div class="back-mark">
    <div class="back-mark__square"></div>
    <div class="back-mark__name">Thornbury<br>Building Company</div>
  </div>

  <div class="identity">
    <h1 class="identity__name">Marcus Thornbury</h1>
    <p class="identity__title">Project Manager</p>
  </div>

  <div class="divider"></div>

  <ul class="contact">
    <li class="contact__item">
      <svg class="contact__icon" viewBox="0 0 24 24" aria-hidden="true"><path fill="#6cb945" d="M6.6 10.8a15.1 15.1 0 0 0 6.6 6.6l2.2-2.2a1 1 0 0 1 1-.25 11.4 11.4 0 0 0 3.6.57 1 1 0 0 1 1 1V20a1 1 0 0 1-1 1A17 17 0 0 1 3 4a1 1 0 0 1 1-1h3.5a1 1 0 0 1 1 1c0 1.25.2 2.45.57 3.57a1 1 0 0 1-.25 1z"/></svg>
      555.274.8136
    </li>
    <li class="contact__item">
      <svg class="contact__icon" viewBox="0 0 24 24" aria-hidden="true"><path fill="#6cb945" d="M2 5h20v14H2z"/><path fill="none" stroke="#222121" stroke-width="2" d="M2 6l10 7 10-7"/></svg>
      thornburybuildingcompany@mailvesta.com
    </li>
    <li class="contact__item">
      <svg class="contact__icon" viewBox="0 0 24 24" aria-hidden="true"><circle cx="12" cy="12" r="10" fill="none" stroke="#6cb945" stroke-width="2.5"/><path fill="none" stroke="#6cb945" stroke-width="2" d="M2 12h20M12 2c3 3 3 17 0 20M12 2c-3 3-3 17 0 20"/></svg>
      thornburybuildingcompany.com
    </li>
  </ul>

  <address class="address">
    487 Larkspur Ln<br>
    Cedar Hollow, OR 95033<br>
    Lic# 2468317
  </address>
</section>

</body>
</html>
```